Business Card Design for Varomir Facility Services

We are looking for a Business Card Design for the Company "Varomir Facility Services."
Front side:
- Company Logo (small)
- Company Name, address, pohone, website and personal data.
- white background, for text e.g. company colors (blue or green like in the logo)
Please use following data:
Company data:
Varomir Facility Services Kostelac
Birkenhaldweg 14
6351 Brunnwil
www.varomir-fs.ch
Person data:
Tarik Kostelac
Geschäftsführer
+41 76 519 47 83
info@varomir-fs.ch
Back side:
could be colored in blue or green
please use a big logo sing and some smaller icons to say what is all beeing offered in facility services, like cleaning, maintenance cleaning
industrial cleaning, caretaking, gardening, disposal. There is no need for everyone of the icons if there are similar or an icon is standing for more of them.
colors to use:
blue: HEX 246BB0
green: HEX 52B33E

```html
<!DOCTYPE html>
<html lang="de">
<head>
<meta charset="utf-8">
<title>Varomir Facility Services – Visitenkarte</title>
<link rel="stylesheet" href="https://fonts.googleapis.com/css2?family=Poppins:wght@400;500;600&display=swap">
<style>
  :root {
    --blue: #246BB0;
    --blue-deep: #0A51B0;
    --green: #52B33E;
    --green-icon: #7DC242;
    --ink: #4a4a4a;
    --rule: #8a8a8a;
    --paper: #ffffff;
    --stage: #e8e5e0;
  }
  * { box-sizing: border-box; margin: 0; padding: 0; }
  html, body { width: 1125px; height: 1200px; overflow: hidden; }
  body {
    background: var(--stage);
    font-family: "Poppins", sans-serif;
    position: relative;
  }
  .card {
    position: absolute;
    left: 151px;
    width: 824px;
    height: 470px;
    box-shadow: 0 3px 8px rgba(0,0,0,.25);
    overflow: hidden;
  }
  .card--front { top: 99px; background: var(--paper); }
  .card--back  { top: 632px; background: var(--blue-deep); }

  /* wordmark */
  .wordmark {
    position: absolute;
    display: flex;
    align-items: center;
    gap: 14px;
    font-weight: 500;
    line-height: 1.05;
  }
  .wordmark__dot { border-radius: 50%; flex: none; }

  .card--front .wordmark { right: 36px; top: 148px; color: var(--blue); text-align: right; }
  .card--front .wordmark__name { font-size: 46px; letter-spacing: 2px; }
  .card--front .wordmark__sub { font-size: 21px; letter-spacing: 3px; }
  .card--front .wordmark__dot { width: 22px; height: 22px; background: var(--green); }

  /* person */
  .person { position: absolute; left: 34px; top: 260px; }
  .person__name { font-size: 30px; font-weight: 600; color: var(--blue-deep); line-height: 36px; }
  .person__role { font-size: 20px; color: var(--green); line-height: 24px; }

  .divider {
    position: absolute; left: 34px; right: 36px; top: 332px;
    border-top: 1px solid var(--rule);
  }
  .contact {
    position: absolute; left: 34px; top: 351px;
    list-style: none; font-size: 19px; color: var(--ink); line-height: 26px;
  }
  .contact li { display: flex; align-items: center; gap: 10px; }
  .contact svg { width: 18px; height: 18px; flex: none; }
  .address {
    position: absolute; right: 36px; top: 352px;
    font-size: 19px; color: var(--ink); line-height: 25px; text-align: right;
    font-style: normal;
  }
  .edge-band { position: absolute; left: 0; bottom: 0; width: 824px; height: 8px; }

  /* back */
  .card--back .wordmark { left: 0; right: 0; top: 140px; justify-content: center; color: #fff; }
  .card--back .wordmark__name { font-size: 54px; letter-spacing: 2px; }
  .card--back .wordmark__sub { font-size: 25px; letter-spacing: 4px; }
  .card--back .wordmark__dot { width: 28px; height: 28px; background: #fff; }

  .services {
    position: absolute; left: 0; top: 312px; width: 100%;
    list-style: none;
  }
  .service {
    position: absolute; width: 140px; margin-left: -70px;
    text-align: center; color: var(--green-icon);
    font-size: 17px; line-height: 21px;
  }
  .service__badge {
    width: 78px; height: 78px; margin: 0 auto 10px;
    border: 2px solid var(--green-icon); border-radius: 50%;
    display: flex; align-items: center; justify-content: center;
  }
  .service__art {
    width: 40px; height: 40px; border-radius: 50%;
    background: var(--green-icon); opacity: .85;
  }
</style>
</head>
<body>

<section class="card card--front" aria-label="Vorderseite">
  <div class="wordmark">
    <div>
      <div class="wordmark__name">VAROMIR</div>
      <div class="wordmark__sub">FACILITY SERVICES</div>
    </div>
    <span class="wordmark__dot"></span>
  </div>

  <div class="person">
    <h1 class="person__name">Tarik Kostelac</h1>
    <p class="person__role">Geschäftsführer</p>
  </div>

  <div class="divider"></div>

  <ul class="contact">
    <li>
      <svg viewBox="0 0 18 18" aria-hidden="true"><rect x="4" y="1" width="10" height="16" rx="2" fill="none" stroke="var(--blue)" stroke-width="2"/><circle cx="9" cy="14" r="1" fill="var(--blue)"/></svg>
      +41 76 519 47 83
    </li>
    <li>
      <svg viewBox="0 0 18 18" aria-hidden="true"><rect x="1" y="4" width="16" height="11" fill="var(--blue)"/><path d="M1 4 L9 10 L17 4" fill="none" stroke="#fff" stroke-width="1.5"/></svg>
      info@varomir-fs.ch
    </li>
    <li>
      <svg viewBox="0 0 18 18" aria-hidden="true"><circle cx="9" cy="9" r="8" fill="var(--blue)"/><path d="M1 9 H17 M9 1 C5 5 5 13 9 17 M9 1 C13 5 13 13 9 17" fill="none" stroke="#fff" stroke-width="1.2"/></svg>
      www.varomir-fs.ch
    </li>
  </ul>

  <address class="address">
    Varomir Facility Services Kostelac<br>
    Birkenhaldweg 14<br>
    6351 Brunnwil
  </address>

  <svg class="edge-band" viewBox="0 0 824 8" preserveAspectRatio="none" aria-hidden="true">
    <polygon points="0,0 538,0 532,8 0,8" fill="var(--blue)"/>
    <polygon points="544,0 824,0 824,8 538,8" fill="var(--green)"/>
  </svg>
</section>

<section class="card card--back" aria-label="Rückseite">
  <div class="wordmark">
    <span class="wordmark__dot"></span>
    <div>
      <div class="wordmark__name">VAROMIR</div>
      <div class="wordmark__sub">FACILITY SERVICES</div>
    </div>
  </div>

  <ul class="services">
    <li class="service" style="left:104px">
      <div class="service__badge"><div class="service__art" role="img" aria-label="Besen-Symbol für Reinigung"></div></div>
      Cleaning
    </li>
    <li class="service" style="left:223px">
      <div class="service__badge"><div class="service__art" role="img" aria-label="Hauswart-Symbol für Hauswartung"></div></div>
      Caretaking
    </li>
    <li class="service" style="left:358px">
      <div class="service__badge"><div class="service__art" role="img" aria-label="Handschuh-Symbol für Unterhaltsreinigung"></div></div>
      Maintenance<br>cleaning
    </li>
    <li class="service" style="left:486px">
      <div class="service__badge"><div class="service__art" role="img" aria-label="Reinigungsmaschinen-Symbol für Industriereinigung"></div></div>
      Industrial<br>cleaning
    </li>
    <li class="service" style="left:605px">
      <div class="service__badge"><div class="service__art" role="img" aria-label="Giesskannen-Symbol für Gartenpflege"></div></div>
      Gardening
    </li>
    <li class="service" style="left:719px">
      <div class="service__badge"><div class="service__art" role="img" aria-label="Abfalleimer-Symbol für Entsorgung"></div></div>
      Disposal
    </li>
  </ul>
</section>

</body>
</html>
```